Awesome photographers card for an awesome new business

Double sided business card Black background and silver logo in middle on one side. Details on otherside. please keep it simple

Industry/Entity Type

Photographer

Contact Information for Business Card

Gerald Fenwick
0452817360
GeraldFenwickPhotography47@mailbox.test
www.GeraldFenwickPhotography.test.au
Instagram _Gerald_fenwick

Requirements
Must have
• My logo in Silver
• please use instagram logo instead of "Instagram"

```html
<!DOCTYPE html>
<html lang="en">
<head>
<meta charset="utf-8">
<title>Gerald Fenwick Photography – Business Card</title>
<link rel="stylesheet" href="https://fonts.googleapis.com/css2?family=Lato:wght@400;700&display=swap">
<style>
  :root {
    --canvas-bg: #2b2b2b;
    --card-bg: #111111;
    --card-edge: #1c1c1c;
    --silver: #c9c9c9;
    --silver-soft: #a9a9a9;
    --ghost: #070707;
  }
  * { box-sizing: border-box; margin: 0; padding: 0; }
  html, body { width: 1200px; height: 880px; overflow: hidden; }
  body {
    background: var(--canvas-bg);
    font-family: "Lato", Arial, sans-serif;
    position: relative;
  }
  .card {
    position: absolute;
    left: 260px;
    width: 680px;
    height: 389px;
    background: var(--card-bg);
    border: 1px solid var(--card-edge);
    box-shadow: 0 14px 30px rgba(0,0,0,0.55);
    overflow: hidden;
  }
  .card--front { top: 34px; }
  .card--back { top: 457px; }

  .brand {
    position: absolute;
    top: 50%; left: 50%;
    transform: translate(-50%, -50%);
    display: flex;
    align-items: center;
    gap: 16px;
  }
  .brand__dot {
    width: 22px; height: 22px;
    border-radius: 50%;
    background: var(--silver);
  }
  .brand__name {
    color: var(--silver);
    font-weight: 700;
    font-size: 30px;
    letter-spacing: 4px;
    text-transform: uppercase;
  }

  .back__ghost {
    position: absolute;
    left: -20px; top: 40px;
    color: var(--ghost);
    font-weight: 700;
    font-size: 150px;
    line-height: 1;
    white-space: nowrap;
  }
  .details {
    position: absolute;
    left: 300px; top: 150px;
    color: var(--silver);
  }
  .details__name {
    font-weight: 700;
    font-size: 21px;
    letter-spacing: 1px;
    text-transform: uppercase;
    margin-bottom: 14px;
  }
  .details__list { list-style: none; }
  .details__item {
    display: flex;
    align-items: center;
    gap: 8px;
    font-size: 15px;
    line-height: 22px;
    color: var(--silver-soft);
  }
  .details__icon { width: 16px; height: 16px; flex: none; }
  .details__web {
    margin-top: 16px;
    font-size: 15px;
    color: var(--silver-soft);
  }
</style>
</head>
<body>
  <section class="card card--front" aria-label="Business card front">
    <div class="brand">
      <span class="brand__dot"></span>
      <span class="brand__name">Gerald Fenwick</span>
    </div>
  </section>

  <section class="card card--back" aria-label="Business card back">
    <div class="back__ghost" aria-hidden="true">Gerald Fenwick</div>
    <div class="details">
      <h1 class="details__name">Gerald Fenwick</h1>
      <ul class="details__list">
        <li class="details__item">
          <svg class="details__icon" viewBox="0 0 16 16" aria-hidden="true">
            <circle cx="8" cy="8" r="7.2" fill="none" stroke="#a9a9a9" stroke-width="1.2"/>
            <path d="M5.2 4.6l1.4-.3.7 1.7-.9.7a5 5 0 0 0 2.2 2.2l.7-.9 1.7.7-.3 1.4c-3 .3-5.8-2.5-5.5-5.5z" fill="#a9a9a9"/>
          </svg>
          0452817360
        </li>
        <li class="details__item">
          <svg class="details__icon" viewBox="0 0 16 16" aria-hidden="true">
            <circle cx="8" cy="8" r="7.2" fill="none" stroke="#a9a9a9" stroke-width="1.2"/>
            <rect x="4.2" y="5.3" width="7.6" height="5.4" fill="#a9a9a9"/>
            <path d="M4.2 5.3L8 8.4l3.8-3.1" fill="none" stroke="#111" stroke-width="0.9"/>
          </svg>
          GeraldFenwickPhotography47@mailbox.test
        </li>
        <li class="details__item">
          <svg class="details__icon" viewBox="0 0 16 16" aria-hidden="true">
            <circle cx="8" cy="8" r="7.2" fill="none" stroke="#a9a9a9" stroke-width="1.2"/>
            <circle cx="8" cy="8" r="3" fill="#a9a9a9"/>
          </svg>
          _Gerald_fenwick
        </li>
      </ul>
      <p class="details__web">www.GeraldFenwickPhotography.test.au</p>
    </div>
  </section>
</body>
</html>
```